Executive recruiting firm in need of business card design

Executive recruiting firm looking for a sleek, classy and modern business card design; card itself will be square shape, rounded edges and soft touch paper, our colors are dark blues in the navy color scale, silvers and grays. Reference our website for a better idea of our company's feel and goals at Tarvex-Up.com - our company message is "Employee Engagement Begins at Recruitment" this should be on the card

```html
<!DOCTYPE html>
<html lang="en">
<head>
<meta charset="utf-8">
<title>Tarvex-Up Business Card</title>
<link href="https://fonts.googleapis.com/css2?family=Roboto:wght@400&family=Roboto+Condensed:wght@700&display=swap" rel="stylesheet">
<style>
  :root {
    --backdrop: #c4c4c4;
    --navy: #141641;
    --white: #ffffff;
  }
  * { margin: 0; padding: 0; box-sizing: border-box; }
  html, body { width: 1200px; height: 960px; overflow: hidden; }
  body {
    position: relative;
    background: var(--backdrop);
    font-family: "Roboto", Arial, sans-serif;
    color: var(--white);
  }
  .card {
    position: absolute;
    background: var(--navy);
    box-shadow: 0 3px 8px rgba(0,0,0,0.3);
  }
  .card-front { left: 320px; top: 108px; width: 608px; height: 334px; }
  .card-back  { left: 320px; top: 493px; width: 600px; height: 342px; }

  .brand-name {
    position: absolute;
    left: 0; top: 134px; width: 100%;
    text-align: center;
    font-family: "Roboto", Arial, sans-serif;
    font-weight: 400;
    font-size: 40px;
    line-height: 1;
    color: var(--white);
  }
  .slogan {
    position: absolute; left: 0; top: 282px; width: 100%;
    text-align: center; font-size: 14.5px;
  }

  .holder {
    position: absolute; right: 328px; top: 143px; text-align: right;
  }
  .holder-name {
    font-family: "Roboto Condensed", Arial, sans-serif;
    font-weight: 700; font-size: 31px; line-height: 1; letter-spacing: 0.3px;
  }
  .holder-role { font-size: 15px; margin-top: 6px; }
  .divider {
    position: absolute; left: 299px; top: 114px; width: 2px; height: 112px;
    background: linear-gradient(to bottom, transparent, var(--white) 20%, var(--white) 80%, transparent);
  }
  .contacts {
    position: absolute; left: 326px; top: 123px; list-style: none;
  }
  .contacts li {
    display: flex; align-items: center; gap: 8px;
    font-size: 14.5px; height: 19.3px;
  }
  .contacts svg { width: 14px; height: 14px; fill: var(--white); flex: none; }
  .address {
    position: absolute; left: 0; top: 279px; width: 100%;
    display: flex; justify-content: center; align-items: center; gap: 4px;
    font-size: 14.5px;
  }
  .address svg { width: 12px; height: 16px; fill: var(--white); }
</style>
</head>
<body>
  <section class="card card-front">
    <p class="brand-name">Tarvex Up</p>
    <p class="slogan">Employee Engagement Begins at Recruitment</p>
  </section>

  <section class="card card-back">
    <div class="holder">
      <p class="holder-name">DANIEL REYES</p>
      <p class="holder-role">CEO/FOUNDER</p>
    </div>
    <div class="divider"></div>
    <ul class="contacts">
      <li><svg viewBox="0 0 24 24"><path d="M6.6 10.8a15.1 15.1 0 0 0 6.6 6.6l2.2-2.2c.3-.3.7-.4 1-.2 1.1.4 2.3.6 3.6.6.6 0 1 .4 1 1V20c0 .6-.4 1-1 1A17 17 0 0 1 3 4c0-.6.4-1 1-1h3.5c.6 0 1 .4 1 1 0 1.300.2 2.5.6 3.6.1.3 0 .7-.2 1z"/></svg>614 290 3875</li>
      <li><svg viewBox="0 0 24 24"><path d="M7 1h10a2 2 0 0 1 2 2v18a2 2 0 0 1-2 2H7a2 2 0 0 1-2-2V3a2 2 0 0 1 2-2zm0 3v14h10V4zm5 15.5a1.2 1.2 0 1 0 0 2.4 1.2 1.2 0 0 0 0-2.4z"/></svg>752 381 4096</li>
      <li><svg viewBox="0 0 24 24"><path d="M6 2h12v6H6zM3 9h18a1 1 0 0 1 1 1v8h-4v4H6v-4H2v-8a1 1 0 0 1 1-1zm5 7v4h8v-4z"/></svg>419 527 6083</li>
      <li><svg viewBox="0 0 24 24"><path d="M2 5h20v14H2zm2 2v.5l8 5 8-5V7zm0 2.8V17h16V9.8l-8 5z"/></svg>daniel@tarvex-up.com</li>
      <li><svg viewBox="0 0 24 24"><path d="M12 2a10 10 0 1 0 0 20 10 10 0 0 0 0-20zm-1 17.9A8 8 0 0 1 4.2 10L9 14.8v1.2a2 2 0 0 0 2 2zm6.9-2.5A2 2 0 0 0 16 16h-1v-3a1 1 0 0 0-1-1H8v-2h2a1 1 0 0 0 1-1V7h2a2 2 0 0 0 2-2v-.4a8 8 0 0 1 2.9 12.8z"/></svg>www.tarvex-up.com</li>
    </ul>
    <p class="address"><svg viewBox="0 0 12 16"><path d="M6 0a6 6 0 0 0-6 6c0 4.5 6 10 6 10s6-5.5 6-10a6 6 0 0 0-6-6zm0 8.5A2.5 2.5 0 1 1 6 3.5a2.5 2.5 0 0 1 0 5z"/></svg>240 Harbor Crest Ave., Linden Bay, CA</p>
  </section>
</body>
</html>
```